Roofing Contractor business card redesign

I want to redesign my business card with a fresh, eye catching concept

Target Market(s)

Residential Roofing Clients, potential employees, and subcontractors.

Industry/Entity Type

Business

Colors

Designer to choose colors to be used in the design.

Requirements
Nice to have
• I just want something that's more pleasing to the eye. You can use a combination of either / or of my logos.

```html
<!DOCTYPE html>
<html lang="en">
<head>
<meta charset="utf-8">
<title>Steady Hands General Contractors – Business Card</title>
<link href="https://fonts.googleapis.com/css2?family=Roboto+Condensed:wght@700&family=Roboto:wght@400;500&family=Open+Sans:wght@700&display=swap" rel="stylesheet">
<style>
  :root {
    --page-bg: #e9e6e2;
    --card-dark: #1f2022;
    --card-light: #f7f7f6;
    --brand-brown: #4a1912;
    --brand-orange: #e8731e;
    --text-grey: #444446;
    --rule-grey: #9a9a9a;
    --white: #ffffff;
  }
  * { margin: 0; padding: 0; box-sizing: border-box; }
  html, body { width: 1200px; height: 960px; overflow: hidden; }
  body { background: var(--page-bg); position: relative; font-family: "Roboto", Arial, sans-serif; }

  .card { position: absolute; border-radius: 20px; overflow: hidden; box-shadow: 0 4px 12px rgba(0,0,0,.25); }

  /* Front */
  .card-front { left: 320px; top: 100px; width: 600px; height: 360px; background: var(--card-dark); }
  .front-illustration {
    position: absolute; right: 0; top: 0; width: 370px; height: 100%;
    background: radial-gradient(ellipse at 60% 55%, #5a4330 0%, #3b3430 40%, var(--card-dark) 75%);
  }
  .front-name {
    position: absolute; left: 33px; top: 232px;
    font-family: "Roboto Condensed", "Arial Narrow", sans-serif; font-weight: 700;
    font-size: 48px; color: var(--white); letter-spacing: -0.5px; line-height: 1;
  }
  .front-tagline {
    position: absolute; left: 34px; top: 286px;
    font-family: "Open Sans", Arial, sans-serif; font-weight: 700; font-size: 16px; color: var(--white);
  }
  .front-web {
    position: absolute; left: 34px; top: 308px;
    font-size: 14px; color: var(--white); letter-spacing: 1.6px;
  }

  /* Back */
  .card-back { left: 320px; top: 493px; width: 598px; height: 342px; background: var(--card-light); }
  .back-band { position: absolute; left: 0; bottom: 0; width: 100%; height: 13px; background: var(--brand-brown); border-top: 3px solid var(--brand-orange); }
  .brand { position: absolute; right: 30px; top: 44px; text-align: right; }
  .brand-mark { display: flex; align-items: center; justify-content: flex-end; gap: 8px; }
  .brand-dot { width: 40px; height: 40px; border-radius: 50%; background: var(--brand-orange); }
  .brand-name {
    font-family: "Roboto Condensed", "Arial Narrow", sans-serif; font-weight: 700;
    font-size: 40px; color: var(--brand-brown); line-height: 1;
  }
  .brand-tagline {
    margin-top: 6px; font-family: "Open Sans", Arial, sans-serif; font-weight: 700;
    font-size: 17px; color: var(--brand-brown);
  }
  .person { position: absolute; left: 27px; top: 164px; }
  .person-name {
    font-family: "Roboto Condensed", "Arial Narrow", sans-serif; font-weight: 700;
    font-size: 21px; color: var(--brand-brown); line-height: 1.1;
  }
  .person-role { font-size: 15px; color: var(--brand-orange); line-height: 19px; }
  .divider { position: absolute; left: 27px; top: 238px; width: 540px; height: 1px; background: var(--rule-grey); }
  .contacts { position: absolute; left: 27px; top: 249px; list-style: none; font-size: 14px; color: var(--text-grey); }
  .contacts li { display: flex; align-items: center; gap: 8px; height: 19.5px; }
  .contacts svg { width: 14px; height: 14px; fill: var(--brand-brown); }
  .address { position: absolute; right: 30px; top: 249px; text-align: right; font-size: 14px; color: var(--text-grey); line-height: 19px; }
  .address .web { letter-spacing: 1.2px; }
</style>
</head>
<body>
  <section class="card card-front">
    <div class="front-illustration" role="img" aria-label="Illustration of a team of three contractors holding tools"></div>
    <div class="front-name">Steady Hands</div>
    <div class="front-tagline">General Contractors, Inc.</div>
    <div class="front-web">www.steadyhandstx.com</div>
  </section>

  <section class="card card-back">
    <div class="brand">
      <div class="brand-mark"><span class="brand-dot"></span><span class="brand-name">Steady Hands</span></div>
      <div class="brand-tagline">General Contractors, Inc.</div>
    </div>
    <div class="person">
      <div class="person-name">SAM CALDER</div>
      <div class="person-role">Apex Certified Roof Inspector</div>
      <div class="person-role">Licensed Property Adjuster</div>
    </div>
    <div class="divider"></div>
    <ul class="contacts">
      <li><svg viewBox="0 0 24 24"><path d="M6.6 10.8a15.1 15.1 0 0 0 6.6 6.6l2.2-2.2a1 1 0 0 1 1-.25 11.4 11.4 0 0 0 3.6.57 1 1 0 0 1 1 1V20a1 1 0 0 1-1 1A17 17 0 0 1 3 4a1 1 0 0 1 1-1h3.5a1 1 0 0 1 1 1c0 1.25.2 2.45.57 3.57a1 1 0 0 1-.25 1z"/></svg>(555) 410-2300</li>
      <li><svg viewBox="0 0 24 24"><path d="M7 1h10a2 2 0 0 1 2 2v18a2 2 0 0 1-2 2H7a2 2 0 0 1-2-2V3a2 2 0 0 1 2-2zm0 3v14h10V4z"/></svg>(555) 238-6017</li>
      <li><svg viewBox="0 0 24 24"><path d="M2 5h20v14H2zm2 2v.5l8 5 8-5V7l-8 5z"/></svg>sam@steadyhandstx.com</li>
    </ul>
    <div class="address">
      <div>4180 Meadow Lane Suite 110</div>
      <div>Ridgeview, TX 75001</div>
      <div class="web">www.steadyhandstx.com</div>
    </div>
    <div class="back-band"></div>
  </section>
</body>
</html>
```